Verodex business card

Business card for sustainable investment company called "Verodex". Verodex is an exchange platform selling carbon credits between buyers and sellers. Carbon Credits are an environmental commodity for reducing global carbon emissions.

the card should obviously have our logo and the theme should be sustainability/environment mixed with a trading platform.

Contact Information for Business Card

Logo, Name, Title, Phone, Email

Colors
0054AA
0677BA
7BADD7
CADEEF
E8F1F8
0094D4
00A9DD
6FCCEA
C7EBF8
E9F6FB
00AB8E
00BBA5
67D7C9
C6EFE9
E9F9F6
59FF00
82FF00
B8FF75
E3FFCB
F4FFEA

```html
<!DOCTYPE html>
<html lang="en">
<head>
<meta charset="utf-8">
<title>Verodex business card</title>
<link rel="stylesheet" href="https://fonts.googleapis.com/css2?family=Poppins:wght@400;600&display=swap">
<style>
  :root {
    --stage: #777777;
    --card-light: #ffffff;
    --card-dark: #1e1b1c;
    --ink: #111111;
    --ink-name: #1f3550;
    --accent: #2585e6;
    --mark: #1f8ae8;
    --type-light: #ffffff;
  }
  * { margin: 0; padding: 0; box-sizing: border-box; }
  html, body {
    width: 1064px;
    height: 1200px;
    overflow: hidden;
    background: var(--stage);
    font-family: "Poppins", sans-serif;
  }
  .canvas { position: relative; width: 1064px; height: 1200px; }

  .card { position: absolute; width: 583px; height: 363px; }

  .card-front {
    left: 292px;
    top: 218px;
    background: var(--card-light);
    border-radius: 0 176px 176px 0 / 0 181px 181px 0;
    box-shadow: 2px 2px 3px rgba(0,0,0,0.55);
  }
  .person { position: absolute; left: 46px; top: 56px; }
  .person-name {
    font-weight: 600;
    font-size: 21px;
    letter-spacing: 0.3px;
    color: var(--ink-name);
    line-height: 1.05;
  }
  .person-title {
    font-weight: 400;
    font-size: 17px;
    color: var(--accent);
    line-height: 1.1;
  }
  .contacts {
    position: absolute;
    right: 57px;
    top: 236px;
    list-style: none;
    text-align: right;
  }
  .contact {
    display: flex;
    justify-content: flex-end;
    align-items: center;
    gap: 9px;
    font-size: 17px;
    color: var(--ink);
    line-height: 21px;
  }
  .contact .highlight { color: var(--accent); }
  .contact-icon { width: 15px; height: 15px; flex: none; }

  .card-back {
    left: 263px;
    top: 623px;
    height: 365px;
    background: var(--card-dark);
    border-radius: 176px 0 0 176px / 182px 0 0 182px;
    box-shadow: 2px 2px 3px rgba(0,0,0,0.55);
  }
  .brand {
    position: absolute;
    left: 56px;
    top: 138px;
    display: flex;
    align-items: center;
    gap: 56px;
  }
  .brand-dot {
    width: 88px;
    height: 88px;
    border-radius: 50%;
    background: var(--mark);
  }
  .brand-name {
    font-weight: 600;
    font-size: 64px;
    letter-spacing: 1px;
    color: var(--type-light);
    line-height: 1;
  }
</style>
</head>
<body>
<main class="canvas">
  <section class="card card-front" aria-label="Card front">
    <div class="person">
      <p class="person-name">DANIEL HARLOW</p>
      <p class="person-title">Managing Director</p>
    </div>
    <ul class="contacts">
      <li class="contact">
        <span>044-987 654 321</span>
        <svg class="contact-icon" viewBox="0 0 24 24" aria-hidden="true"><path fill="var(--accent)" d="M6.6 10.8a15.2 15.2 0 0 0 6.6 6.6l2.2-2.2c.3-.3.7-.4 1-.2 1.1.4 2.3.6 3.6.6.6 0 1 .4 1 1V20c0 .6-.4 1-1 1A17 17 0 0 1 3 4c0-.6.4-1 1-1h3.5c.6 0 1 .4 1 1 0 1.3.2 2.5.6 3.6.1.3 0 .7-.2 1z"/><path fill="none" stroke="var(--accent)" stroke-width="2" d="M14 3a7 7 0 0 1 7 7M14 7a3 3 0 0 1 3 3"/></svg>
      </li>
      <li class="contact">
        <span>hello@verodex.com</span>
        <svg class="contact-icon" viewBox="0 0 24 24" aria-hidden="true"><rect x="1" y="5" width="22" height="14" fill="var(--accent)"/><path d="M1 5l11 8 11-8M1 19l8-7M23 19l-8-7" fill="none" stroke="#fff" stroke-width="1.4"/></svg>
      </li>
      <li class="contact">
        <span>www.<span class="highlight">verodextrade</span>.com</span>
        <svg class="contact-icon" viewBox="0 0 24 24" aria-hidden="true"><circle cx="12" cy="12" r="11" fill="var(--accent)"/><g fill="none" stroke="#fff" stroke-width="1.3"><ellipse cx="12" cy="12" rx="4.5" ry="10"/><path d="M2 12h20M3.5 7h17M3.5 17h17M12 2v20"/></g></svg>
      </li>
    </ul>
  </section>

  <section class="card card-back" aria-label="Card back">
    <div class="brand">
      <span class="brand-dot" aria-hidden="true"></span>
      <span class="brand-name">VERODEX</span>
    </div>
  </section>
</main>
</body>
</html>
```